My business is Property developing Stationary

I want business card and stationery. Please have the formate so I can edit details on card and stationary.

Please see my logo and on the back of the card I want it same red as my logo and I will provide copy that I want on the back of the card.

Also need an email signature

On the business card and email signature add below copy:
Project Management- Acquisitions- Syndicates- Joint Ventures

Target Market(s)

Property investors

Industry/Entity Type

Business

Requirements
Must have
• Reflect my Logo

```html
<!DOCTYPE html>
<html lang="en">
<head>
<meta charset="utf-8">
<title>Verano Property Developments – Business Card</title>
<link rel="stylesheet" href="https://fonts.googleapis.com/css2?family=Mulish:wght@400;600;800&display=swap">
<style>
  :root {
    --brand-red: #e8392f;
    --brand-red-light: #f0473c;
    --ink: #2b2b2b;
    --charcoal: #1f1f1f;
    --paper: #f7f7f5;
    --backdrop: #2a2a2a;
    --white: #ffffff;
  }
  * { margin: 0; padding: 0; box-sizing: border-box; }
  html, body { width: 1200px; height: 1000px; overflow: hidden; }
  body {
    background: var(--backdrop);
    font-family: "Mulish", sans-serif;
    position: relative;
  }
  .card {
    position: absolute;
    width: 580px;
    height: 324px;
    overflow: hidden;
  }
  /* Front */
  .card-front { left: 201px; top: 149px; background: var(--paper); }
  .holder { position: absolute; left: 40px; top: 70px; }
  .holder-name {
    color: var(--brand-red);
    font-weight: 800;
    font-size: 19px;
    letter-spacing: 0.5px;
    line-height: 24px;
  }
  .holder-role { color: var(--ink); font-size: 15px; line-height: 20px; }
  .brand {
    position: absolute;
    right: 40px;
    top: 58px;
    text-align: center;
  }
  .brand-name {
    font-weight: 800;
    font-size: 40px;
    line-height: 42px;
    letter-spacing: 1px;
    color: var(--brand-red);
  }
  .brand-tagline {
    font-weight: 800;
    font-size: 14px;
    color: var(--ink);
    line-height: 18px;
  }
  .contact-list {
    position: absolute;
    left: 40px;
    top: 226px;
    list-style: none;
  }
  .contact-item {
    display: flex;
    align-items: center;
    gap: 10px;
    font-size: 13.5px;
    color: var(--ink);
    height: 19px;
  }
  .contact-icon { width: 14px; height: 14px; flex: none; }
  .address {
    position: absolute;
    right: 40px;
    top: 245px;
    text-align: right;
    font-size: 13.5px;
    line-height: 17px;
    color: var(--ink);
    font-style: normal;
  }
  .band { position: absolute; bottom: 0; height: 19px; }
  .band-red { left: 0; width: 272px; background: var(--brand-red); }
  .band-dark { left: 272px; right: 0; background: var(--charcoal); }
  /* Back */
  .card-back {
    left: 419px;
    top: 548px;
    background: linear-gradient(160deg, var(--brand-red-light), var(--brand-red));
    display: flex;
    flex-direction: column;
    align-items: center;
    justify-content: center;
  }
  .card-back .brand-name { color: var(--white); font-size: 46px; line-height: 48px; }
  .card-back .brand-tagline { color: var(--white); font-size: 16px; }
  .card-back .brand { position: static; }
</style>
</head>
<body>
  <section class="card card-front" aria-label="Business card front">
    <div class="holder">
      <p class="holder-name">SAM WHITFIELD</p>
      <p class="holder-role">Managing Director</p>
    </div>

    <div class="brand">
      <p class="brand-name">VERANO</p>
      <p class="brand-tagline">Property Developments</p>
    </div>

    <ul class="contact-list">
      <li class="contact-item">
        <svg class="contact-icon" viewBox="0 0 14 14" aria-hidden="true">
          <rect width="14" height="14" rx="2" fill="var(--brand-red)"/>
          <path d="M4 3.2 L5.6 3 L6.3 5 L5.3 5.8 Q6 7.6 8.2 8.7 L9 7.7 L11 8.4 L10.8 10 Q7.5 10.6 5.2 8.3 Q3.2 6.2 4 3.2Z" fill="var(--white)"/>
        </svg>
        <span>1300 555 210</span>
      </li>
      <li class="contact-item">
        <svg class="contact-icon" viewBox="0 0 14 14" aria-hidden="true">
          <rect width="14" height="14" rx="2" fill="var(--brand-red)"/>
          <rect x="3" y="4" width="8" height="6" fill="none" stroke="var(--white)" stroke-width="1"/>
          <path d="M3 4 L7 7.5 L11 4" fill="none" stroke="var(--white)" stroke-width="1"/>
        </svg>
        <span>info@veranodev.com</span>
      </li>
      <li class="contact-item">
        <svg class="contact-icon" viewBox="0 0 14 14" aria-hidden="true">
          <rect width="14" height="14" rx="2" fill="var(--brand-red)"/>
          <circle cx="7" cy="7" r="4" fill="none" stroke="var(--white)" stroke-width="1"/>
          <ellipse cx="7" cy="7" rx="1.7" ry="4" fill="none" stroke="var(--white)" stroke-width="0.9"/>
          <path d="M3 7 H11" stroke="var(--white)" stroke-width="0.9"/>
        </svg>
        <span>www.veranodev.com</span>
      </li>
    </ul>

    <address class="address">
      Level 12, Harbour House<br>
      18 Quay Lane, Sydney
    </address>

    <div class="band band-red"></div>
    <div class="band band-dark"></div>
  </section>

  <section class="card card-back" aria-label="Business card back">
    <div class="brand">
      <p class="brand-name">VERANO</p>
      <p class="brand-tagline">Property Developments</p>
    </div>
  </section>
</body>
</html>
```